Ecommerce web site design for 80s Retro website

we need a website to sell retro gift boxes based around 80's movies, music and gaming
it needs to work with the cartlantic ecommerce provider
there would only be 3 basic gift boxes (music, movies and gaming) , but the packaging would be able to be chosen to match birthdays, Christmas etc.
Each themed box will also have three levels of pricing, classic, premium, ultimate.
the website should be themed around the same colour scheme and look as the logo.

Target Market(s)

People after retro presents and gifts so probably people in their 40s to 50s

Coding

Coded - Design and coding required

Number of Pages Required

1 page

Requirements
Must have
• A real retro look and feel with bright neon colours and some icons or symbols of things from the 80s like tunepods, joysticks, movies, music, gaming etc
Should not have
• A boring bland interface

```html
<!DOCTYPE html>
<html lang="en">
<head>
<meta charset="utf-8">
<title>Neon Attic – Retro Gift Boxes</title>
<link href="https://fonts.googleapis.com/css2?family=Orbitron:wght@500;600;700;800&family=Roboto:wght@400;500;700&display=swap" rel="stylesheet">
<style>
:root{
  --cyan:#22b5e8;
  --pink:#e6077f;
  --ink:#333a40;
  --muted:#666;
  --page:#f3f4f6;
  --white:#fff;
  --line:#dcdcdc;
  --night:#0f0f2a;
  --violet:#6a2cd8;
  --neon-blue:#1fb6ff;
  --neon-pink:#e23bd0;
  --neon-gold:#ffcc33;
}
*{box-sizing:border-box;margin:0;padding:0}
html,body{width:1200px;height:2545px;overflow:hidden}
body{background:var(--page);font-family:"Roboto",Arial,sans-serif;color:var(--ink);position:relative}
.wrap{position:absolute;left:110px;width:980px}

/* top bar */
.topbar{position:absolute;top:0;left:0;width:1200px;height:56px;background:var(--cyan)}
.topbar ul{list-style:none;position:absolute;right:110px;top:20px;display:flex;gap:44px}
.topbar a{color:var(--white);font-size:13px;font-weight:500;text-decoration:none;letter-spacing:.2px}

/* header */
.header{position:absolute;top:56px;left:0;width:1200px;height:171px;background:var(--white);border-bottom:1px solid #e3e3e3}
.brand{position:absolute;left:110px;top:32px;display:flex;align-items:center;gap:12px}
.brand-dot{width:26px;height:26px;border-radius:50%;background:var(--pink)}
.brand-name{font-family:"Orbitron",sans-serif;font-weight:800;font-size:27px;color:var(--pink);letter-spacing:1px}
.search{position:absolute;left:651px;top:30px;width:375px;height:47px;border:1px solid #bbb;border-radius:3px}
.search span{position:absolute;left:18px;top:15px;font-size:14px;color:#555}
.search svg{position:absolute;right:14px;top:16px}
.header-icons{position:absolute;left:1039px;top:44px;display:flex;gap:10px}
.header-rule{position:absolute;left:110px;top:105px;width:980px;height:1px;background:var(--line)}
.mainnav{position:absolute;left:164px;top:133px;display:flex;gap:61px;list-style:none}
.mainnav a{font-family:"Orbitron",sans-serif;font-size:13.5px;font-weight:600;color:var(--ink);text-decoration:none;letter-spacing:.4px}
.mainnav a.active{color:var(--pink)}
.nav-sep{position:absolute;left:842px;top:129px;width:1px;height:22px;background:var(--cyan)}
.basket{position:absolute;left:870px;top:132px;font-size:15px;font-weight:500;display:flex;gap:10px;align-items:center}
.basket-count{position:absolute;right:-1px;top:-15px;color:var(--pink);font-size:12px}

/* hero */
.hero{top:272px;height:532px;background:var(--white);padding:6px;box-shadow:0 0 4px rgba(0,0,0,.12)}
.hero-art{position:relative;width:100%;height:100%;overflow:hidden;
  background:
    radial-gradient(circle at 26% 22%,rgba(255,204,51,.35) 0,rgba(255,204,51,0) 22%),
    radial-gradient(ellipse at 26% 62%,rgba(31,182,255,.45) 0,rgba(31,182,255,0) 32%),
    radial-gradient(ellipse at 26% 80%,rgba(226,59,208,.45) 0,rgba(226,59,208,0) 30%),
    radial-gradient(ellipse at 70% 50%,rgba(106,44,216,.45) 0,rgba(106,44,216,0) 45%),
    linear-gradient(160deg,#1c1a4e 0%,#17163e 45%,var(--night) 100%)}
.hero-copy{position:absolute;left:488px;top:182px;width:440px;text-align:center;color:var(--white)}
.hero-title{font-family:"Orbitron",sans-serif;font-weight:700;font-size:47px;color:#d53aac;letter-spacing:2px;line-height:56px}
.hero-text{margin-top:18px;font-size:16.5px;line-height:26px}
.btn-shop{display:inline-block;margin-top:24px;width:154px;height:52px;line-height:52px;border-radius:26px;background:var(--cyan);font-family:"Orbitron",sans-serif;font-size:14px;font-weight:600;color:var(--white)}
.dots{position:absolute;left:432px;bottom:18px;display:flex;gap:6px}
.dots i{width:30px;height:3px;background:var(--white)}
.dots i.on{background:var(--pink)}

/* sections */
.section-title{position:absolute;left:0;width:1200px;text-align:center;font-family:"Orbitron",sans-serif;font-weight:600;font-size:22px;letter-spacing:1px;color:var(--ink)}
.section-title::after{content:"";display:block;width:38px;height:2px;background:var(--cyan);margin:14px auto 0}

.plans{top:905px;display:flex;gap:22px}
.plan{width:312px;text-align:center}
.plan-frame{height:316px;background:var(--white);padding:6px;box-shadow:0 0 4px rgba(0,0,0,.12)}
.plan-art{height:100%;position:relative}
.plan-art.music{background:
  radial-gradient(ellipse at 50% 62%,#3aa6dd 0,#4fb2e0 22%,rgba(79,178,224,0) 40%),
  radial-gradient(circle at 48% 30%,rgba(226,160,40,.7) 0,rgba(226,160,40,0) 16%),
  radial-gradient(circle at 78% 78%,rgba(160,200,60,.6) 0,rgba(160,200,60,0) 14%),
  linear-gradient(180deg,#a2d6ec,#88cbe6)}
.plan-art.movies{background:
  radial-gradient(ellipse at 50% 58%,#1b1b1b 0,#262626 24%,rgba(38,38,38,0) 38%),
  radial-gradient(circle at 50% 28%,rgba(200,150,40,.8) 0,rgba(200,150,40,0) 18%),
  linear-gradient(180deg,#f7b3dc,#f3a6d6)}
.plan-art.gaming{background:
  radial-gradient(ellipse at 58% 64%,#f58a7e 0,#f3a4c4 20%,rgba(243,164,196,0) 36%),
  radial-gradient(circle at 32% 40%,rgba(240,230,120,.7) 0,rgba(240,230,120,0) 12%),
  radial-gradient(circle at 24% 70%,rgba(255,255,255,.6) 0,rgba(255,255,255,0) 10%),
  linear-gradient(180deg,#5fd6ea,#6ad9ef)}
.plan-art b{position:absolute;top:14px;left:0;width:100%;font-family:"Roboto",sans-serif;font-weight:700;font-size:44px;letter-spacing:1px;color:rgba(255,255,255,.5)}
.plan-name{margin-top:22px;font-size:19px;font-weight:500;color:var(--ink)}
.btn-plan{display:inline-block;margin-top:14px;width:98px;height:35px;line-height:35px;background:var(--cyan);color:var(--white);font-size:11.5px;font-weight:500}
.btn-plan.hot{background:var(--pink)}

.grid{display:flex;flex-wrap:wrap;gap:39px 13px}
.row1{top:1468px}
.product{width:235px;height:306px;background:var(--white);padding:7px;box-shadow:0 0 4px rgba(0,0,0,.12)}
.product-art{height:196px;background:#eeeeef}
.product-art.blue{background:radial-gradient(ellipse at 38% 40%,#2a2a2a 0,rgba(42,42,42,0) 14%),radial-gradient(ellipse at 45% 62%,#8fd0ea 0,#aadcf0 22%,rgba(170,220,240,0) 40%),radial-gradient(circle at 74% 50%,#3a9cc4 0,rgba(58,156,196,0) 20%),#eeeeef}
.product-art.pink{background:radial-gradient(ellipse at 30% 30%,#555 0,rgba(85,85,85,0) 12%),radial-gradient(ellipse at 45% 62%,#e88fc4 0,#f1b4d6 22%,rgba(241,180,214,0) 40%),radial-gradient(circle at 74% 50%,#b3307c 0,rgba(179,48,124,0) 20%),#eeeeef}
.product-art.rose{background:radial-gradient(ellipse at 35% 28%,#c9ccc4 0,rgba(201,204,196,0) 15%),radial-gradient(ellipse at 45% 64%,#e7a9ae 0,#efc4c8 22%,rgba(239,196,200,0) 40%),radial-gradient(circle at 74% 50%,#8a3037 0,rgba(138,48,55,0) 20%),#eeeeef}
.product-art.sand{background:radial-gradient(ellipse at 30% 30%,#111 0,rgba(17,17,17,0) 16%),radial-gradient(ellipse at 45% 64%,#d4c4b0 0,#e2d6c8 22%,rgba(226,214,200,0) 40%),radial-gradient(circle at 74% 50%,#7a5a3c 0,rgba(122,90,60,0) 20%),#eeeeef}
.product-art.sage{background:radial-gradient(ellipse at 38% 30%,#e98a1e 0,rgba(233,138,30,0) 15%),radial-gradient(ellipse at 45% 64%,#bcdcae 0,#cfe5c4 22%,rgba(207,229,196,0) 40%),radial-gradient(circle at 74% 50%,#55783e 0,rgba(85,120,62,0) 20%),#eeeeef}
.product-art.lilac{background:radial-gradient(ellipse at 35% 28%,#666 0,rgba(102,102,102,0) 14%),radial-gradient(ellipse at 45% 62%,#d2b8e6 0,#e0cdee 22%,rgba(224,205,238,0) 40%),radial-gradient(circle at 74% 50%,#7a3c9e 0,rgba(122,60,158,0) 20%),#eeeeef}
.product-art.red{background:radial-gradient(ellipse at 45% 26%,#222 0,rgba(34,34,34,0) 16%),radial-gradient(ellipse at 45% 62%,#fafafa 0,#e2e2e2 24%,rgba(226,226,226,0) 40%),radial-gradient(circle at 62% 60%,#e3221b 0,rgba(227,34,27,0) 18%),#eeeeef}
.product-head{display:flex;justify-content:space-between;align-items:center;margin:20px 0 0 7px}
.product-name{font-size:16.5px;font-weight:500;color:var(--ink)}
.wish{width:32px;height:32px;border-radius:50%;background:#f3f3f3;display:flex;align-items:center;justify-content:center}
.price{margin:10px 0 0 7px;font-size:19px}
.price s{color:var(--muted)}
.price em{font-style:normal;color:var(--pink);margin-left:6px}

/* newsletter */
.newsletter{position:absolute;top:2200px;left:0;width:1200px;height:141px;background:var(--cyan)}
.newsletter h2{position:absolute;left:122px;top:46px;font-family:"Orbitron",sans-serif;font-weight:600;font-size:20px;color:var(--white);letter-spacing:.5px}
.newsletter p{position:absolute;left:122px;top:80px;font-size:17px;color:var(--white)}
.signup{position:absolute;left:566px;top:44px;width:524px;height:53px;background:var(--white);border-radius:3px;overflow:hidden}
.signup span{position:absolute;left:20px;top:18px;font-size:14px;color:#444}
.signup b{position:absolute;right:0;top:0;width:104px;height:53px;line-height:53px;text-align:center;background:var(--pink);color:var(--white);font-size:14px;font-weight:500}

/* footer */
.footnav{position:absolute;top:2386px;left:296px;display:flex;gap:57px;list-style:none}
.footnav a{font-family:"Orbitron",sans-serif;font-size:12.5px;font-weight:600;color:#555;text-decoration:none;letter-spacing:.3px}
.payments{position:absolute;top:2433px;left:458px;display:flex;gap:5px}
.payments i{width:43px;height:27px;background:var(--white);border:1px solid #ddd;display:block}
.copyright{position:absolute;top:2485px;left:0;width:1200px;text-align:center;font-size:16px;color:#444}
</style>
</head>
<body>

<div class="topbar">
  <ul>
    <li><a href="#">GIFT VOUCHER</a></li>
    <li><a href="#">YOUR ACCOUNT</a></li>
    <li><a href="#">REGISTER</a></li>
    <li><a href="#">LOGIN</a></li>
  </ul>
</div>

<header class="header">
  <div class="brand"><span class="brand-dot"></span><span class="brand-name">NEON ATTIC</span></div>
  <div class="search"><span>Search for Products</span>
    <svg width="14" height="14" viewBox="0 0 14 14"><circle cx="6" cy="6" r="4.3" fill="none" stroke="#333" stroke-width="2"/><line x1="9" y1="9" x2="12.5" y2="12.5" stroke="#333" stroke-width="2"/></svg>
  </div>
  <div class="header-icons">
    <svg width="20" height="20" viewBox="0 0 20 20"><circle cx="10" cy="6" r="4" fill="none" stroke="#333" stroke-width="1.6"/><path d="M3 18c0-4 3-6 7-6s7 2 7 6z" fill="none" stroke="#333" stroke-width="1.6"/></svg>
    <svg width="20" height="20" viewBox="0 0 20 20"><path d="M10 17 3 10a4 4 0 0 1 7-5 4 4 0 0 1 7 5z" fill="none" stroke="#333" stroke-width="1.6"/></svg>
  </div>
  <div class="header-rule"></div>
  <ul class="mainnav">
    <li><a href="#" class="active">HOME</a></li>
    <li><a href="#">ABOUT US</a></li>
    <li><a href="#">SERVICES</a></li>
    <li><a href="#">NEWS</a></li>
    <li><a href="#">CONTACT US</a></li>
  </ul>
  <div class="nav-sep"></div>
  <div class="basket">BASKET (0 ITEMS)
    <svg width="17" height="16" viewBox="0 0 17 16"><path d="M0 1h3l2 9h9l2-7H4" fill="var(--pink)" stroke="var(--pink)" stroke-width="1.5"/><circle cx="6" cy="14" r="1.5" fill="var(--pink)"/><circle cx="13" cy="14" r="1.5" fill="var(--pink)"/></svg>
    <span class="basket-count">0</span>
  </div>
</header>

<section class="wrap hero">
  <div class="hero-art" role="img" aria-label="Neon illustration of an open gift box with glowing gold stars against a dark brick wall">
    <div class="hero-copy">
      <h1 class="hero-title">NEON ATTIC</h1>
      <p class="hero-text">Sed ut perspiciatis tunde omnis iste natus error sit&nbsp; accu santium doloremque laudantium, totam</p>
      <a class="btn-shop">SHOP NOW</a>
    </div>
    <div class="dots"><i></i><i class="on"></i><i></i></div>
  </div>
</section>

<h2 class="section-title" style="top:840px">PRICING PLAN</h2>
<section class="wrap plans">
  <div class="plan">
    <div class="plan-frame"><div class="plan-art music" role="img" aria-label="Blue gift box with gold ribbon and festive decorations"><b>MUSIC</b></div></div>
    <p class="plan-name">CLASSIC PLAN</p>
    <a class="btn-plan">VIEW DETAILS</a>
  </div>
  <div class="plan">
    <div class="plan-frame"><div class="plan-art movies" role="img" aria-label="Black clapperboard gift box wrapped in gold film-strip ribbon"><b>MOVIES</b></div></div>
    <p class="plan-name">PREMIUM PLAN</p>
    <a class="btn-plan hot">VIEW DETAILS</a>
  </div>
  <div class="plan">
    <div class="plan-frame"><div class="plan-art gaming" role="img" aria-label="Pink surprise box with balloons and confetti"><b>GAMING</b></div></div>
    <p class="plan-name">ULTIMATE PLAN</p>
    <a class="btn-plan">VIEW DETAILS</a>
  </div>
</section>

<h2 class="section-title" style="top:1396px">FEATURED PRODUCTS</h2>
<section class="wrap grid row1">
  <div class="product"><div class="product-art blue" role="img" aria-label="Video cassette in a blue gift box"></div><div class="product-head"><span class="product-name">PRODUCT NAME</span><span class="wish"><svg width="12" height="11" viewBox="0 0 20 18"><path d="M10 16 3 9a4 4 0 0 1 7-5 4 4 0 0 1 7 5z" fill="none" stroke="var(--cyan)" stroke-width="2"/></svg></span></div><p class="price"><s>£39.95</s><em>£29.95</em></p></div>
  <div class="product"><div class="product-art pink" role="img" aria-label="Walkie-talkies in a pink gift box"></div><div class="product-head"><span class="product-name">PRODUCT NAME</span><span class="wish"><svg width="12" height="11" viewBox="0 0 20 18"><path d="M10 16 3 9a4 4 0 0 1 7-5 4 4 0 0 1 7 5z" fill="none" stroke="var(--cyan)" stroke-width="2"/></svg></span></div><p class="price"><s>£39.95</s><em>£29.95</em></p></div>
  <div class="product"><div class="product-art blue" role="img" aria-label="Boombox in a blue gift box"></div><div class="product-head"><span class="product-name">PRODUCT NAME</span><span class="wish"><svg width="12" height="11" viewBox="0 0 20 18"><path d="M10 16 3 9a4 4 0 0 1 7-5 4 4 0 0 1 7 5z" fill="none" stroke="var(--cyan)" stroke-width="2"/></svg></span></div><p class="price"><s>£39.95</s><em>£29.95</em></p></div>
  <div class="product"><div class="product-art rose" role="img" aria-label="Handheld game console in a rose gift box"></div><div class="product-head"><span class="product-name">PRODUCT NAME</span><span class="wish"><svg width="12" height="11" viewBox="0 0 20 18"><path d="M10 16 3 9a4 4 0 0 1 7-5 4 4 0 0 1 7 5z" fill="none" stroke="var(--cyan)" stroke-width="2"/></svg></span></div><p class="price"><s>£39.95</s><em>£29.95</em></p></div>
  <div class="product"><div class="product-art sand" role="img" aria-label="Game console and controller in a beige gift box"></div><div class="product-head"><span class="product-name">PRODUCT NAME</span><span class="wish"><svg width="12" height="11" viewBox="0 0 20 18"><path d="M10 16 3 9a4 4 0 0 1 7-5 4 4 0 0 1 7 5z" fill="none" stroke="var(--cyan)" stroke-width="2"/></svg></span></div><p class="price"><s>£39.95</s><em>£29.95</em></p></div>
  <div class="product"><div class="product-art sage" role="img" aria-label="Retro television in a green gift box"></div><div class="product-head"><span class="product-name">PRODUCT NAME</span><span class="wish"><svg width="12" height="11" viewBox="0 0 20 18"><path d="M10 16 3 9a4 4 0 0 1 7-5 4 4 0 0 1 7 5z" fill="none" stroke="var(--cyan)" stroke-width="2"/></svg></span></div><p class="price"><s>£39.95</s><em>£29.95</em></p></div>
  <div class="product"><div class="product-art lilac" role="img" aria-label="Audio cassette in a lilac gift box"></div><div class="product-head"><span class="product-name">PRODUCT NAME</span><span class="wish"><svg width="12" height="11" viewBox="0 0 20 18"><path d="M10 16 3 9a4 4 0 0 1 7-5 4 4 0 0 1 7 5z" fill="none" stroke="var(--cyan)" stroke-width="2"/></svg></span></div><p class="price"><s>£39.95</s><em>£29.95</em></p></div>
  <div class="product"><div class="product-art red" role="img" aria-label="Portable radio in a white gift box with red bow"></div><div class="product-head"><span class="product-name">PRODUCT NAME</span><span class="wish"><svg width="12" height="11" viewBox="0 0 20 18"><path d="M10 16 3 9a4 4 0 0 1 7-5 4 4 0 0 1 7 5z" fill="none" stroke="var(--cyan)" stroke-width="2"/></svg></span></div><p class="price"><s>£39.95</s><em>£29.95</em></p></div>
</section>

<section class="newsletter">
  <h2>WHAT'S NEW WITH US?</h2>
  <p>Sed ut perspiciatis unde omnis iste natus error sit</p>
  <div class="signup"><span>Enter Your Email :</span><b>SUBSCRIBE</b></div>
</section>

<footer>
  <ul class="footnav">
    <li><a href="#">HOME</a></li>
    <li><a href="#">ABOUT US</a></li>
    <li><a href="#">SERVICES</a></li>
    <li><a href="#">NEWS</a></li>
    <li><a href="#">CONTACT US</a></li>
  </ul>
  <div class="payments" aria-label="Accepted payment methods"><i></i><i></i><i></i><i></i><i></i><i></i></div>
  <p class="copyright">Neon Attic © 2022.All Rights Reserved.</p>
</footer>

</body>
</html>
```